Real estate broker business card

Want a modern celan but effective business card for my residential and commercial real estate business. I want the back of the card to advertise my services and to capture business. I have attached the back of my current business card fore ideas
Updates

Logos, photo and text updates added! Added Saturday, September 3, 2016

Project Deadline Extended Reason: LOGOS, PHOTOS AND TEST JUST UPLOADED! I'M READY TO PICK A DESIGN! THANK YOU! Added Saturday, September 3, 2016

Target Market(s)

home buyers and seller. commercial buyers and sellers

Industry/Entity Type

Real Estate

Contact Information for Business Card

must have my contact information and my photo

Requirements
Must have
• Carla Ventrino
• Owner & Qualifying Broker
• Ventrino Real Estate Services
• 505.718.2094
• carla@ventrinohomes.example
• www.ventrinohomes.example
Nice to have
• metallic
• Business capture text: " Don't buy or lease property without someone looking out for your best interests. I will represent you on your home or investment purchase for FREE!"
• "Home owners, call today to receive a FREE market analysis for your homes value!

```html
<!DOCTYPE html>
<html lang="en">
<head>
<meta charset="utf-8">
<title>Ventrino Real Estate Services – Business Card</title>
<link href="https://fonts.googleapis.com/css2?family=Open+Sans:wght@400;600;700&display=swap" rel="stylesheet">
<style>
  :root {
    --page-bg: #ecebe9;
    --card-clear: #f6f5f3;
    --teal-light: #2fb0c4;
    --teal-mid: #1f93a6;
    --teal-dark: #13707f;
    --teal-text: #1c7d8c;
    --silver-light: #f7f7f7;
    --silver-mid: #d9dbdc;
    --silver-dark: #a9adaf;
    --faint: #c6cbcd;
    --ink: #222629;
    --white: #ffffff;
  }
  * { margin: 0; padding: 0; box-sizing: border-box; }
  html, body {
    width: 1200px; height: 900px; overflow: hidden;
    background: var(--page-bg);
    font-family: "Open Sans", Arial, sans-serif;
  }
  .canvas { position: relative; width: 1200px; height: 900px; }

  .card {
    position: absolute;
    width: 557px; height: 343px;
    display: flex;
    box-shadow: 0 6px 18px rgba(0,0,0,0.12);
  }
  .card--front { left: 237px; top: 62px; }
  .card--back  { left: 459px; top: 518px; }

  /* front */
  .brand-panel {
    width: 278px; height: 100%;
    background: var(--card-clear);
    display: flex; flex-direction: column; align-items: center;
    padding-top: 104px;
  }
  .brand-mark {
    width: 46px; height: 46px; border-radius: 50%;
    background: var(--teal-mid);
  }
  .brand-name {
    color: var(--teal-text);
    font-weight: 600;
    font-size: 40px;
    letter-spacing: 2.5px;
    line-height: 1;
    margin-top: 62px;
  }
  .brand-tagline {
    color: var(--teal-text);
    font-weight: 600;
    font-size: 13px;
    letter-spacing: 3.6px;
    margin-top: 8px;
  }
  .contact-panel {
    flex: 1;
    background: linear-gradient(180deg, var(--teal-dark) 0%, var(--teal-light) 45%, var(--teal-mid) 80%, var(--teal-dark) 100%);
    color: var(--white);
    padding: 86px 0 0 31px;
  }
  .person-name { font-size: 17px; font-weight: 600; line-height: 1.2; }
  .person-title { font-size: 14.5px; line-height: 1.4; }
  .company { font-size: 14.5px; margin-top: 38px; margin-bottom: 4px; }
  .contact-list { list-style: none; font-size: 14.5px; line-height: 20px; }
  .contact-list li { display: flex; align-items: center; gap: 8px; }
  .contact-list svg { width: 12px; height: 12px; flex: none; }

  /* back */
  .feature-panel {
    width: 279px; height: 100%;
    background: linear-gradient(180deg, var(--silver-light) 0%, var(--silver-mid) 60%, var(--silver-dark) 100%);
    display: flex; flex-direction: column; align-items: center;
    padding-top: 92px;
  }
  .feature-mark {
    width: 64px; height: 64px;
    background: var(--teal-mid);
  }
  .feature-name {
    color: var(--teal-text);
    font-weight: 600; font-size: 38px; letter-spacing: 2.5px;
    line-height: 1;
    margin-top: 26px;
  }
  .feature-url {
    margin-top: auto; margin-bottom: 44px;
    font-size: 15px; color: var(--ink);
  }
  .faint-panel {
    flex: 1;
    background: var(--card-clear);
    display: flex; flex-direction: column; align-items: center;
    padding-top: 110px;
  }
  .faint-panel .brand-mark { background: var(--faint); }
  .faint-panel .brand-name { color: var(--faint); margin-top: 48px; font-size: 36px; }
  .faint-panel .brand-tagline { color: var(--faint); font-size: 12px; letter-spacing: 3.2px; }
</style>
</head>
<body>
<main class="canvas">

  <section class="card card--front" aria-label="Business card front">
    <div class="brand-panel">
      <span class="brand-mark" aria-hidden="true"></span>
      <div class="brand-name">VENTRINO</div>
      <div class="brand-tagline">REAL ESTATE SERVICES</div>
    </div>
    <div class="contact-panel">
      <div class="person-name">Carla Ventrino</div>
      <div class="person-title">Owner &amp; Qualifying Broker</div>
      <div class="company">Ventrino Real Estate Services</div>
      <ul class="contact-list">
        <li>
          <svg viewBox="0 0 24 24" aria-hidden="true"><path fill="#ffffff" d="M6.6 10.8a15.1 15.1 0 0 0 6.6 6.6l2.2-2.2c.3-.3.7-.4 1-.2 1.1.4 2.3.6 3.6.6.6 0 1 .4 1 1V20c0 .6-.4 1-1 1A17 17 0 0 1 3 4c0-.6.4-1 1-1h3.5c.6 0 1 .4 1 1 0 1.3.2 2.5.6 3.6.1.3 0 .7-.2 1z"/></svg>
          505.718.2094
        </li>
        <li>
          <svg viewBox="0 0 24 24" aria-hidden="true"><rect x="2" y="5" width="20" height="14" fill="#ffffff"/><path d="M2 5l10 8 10-8" fill="none" stroke="#1f93a6" stroke-width="2"/></svg>
          carla@ventrinohomes.example
        </li>
        <li>
          <svg viewBox="0 0 24 24" aria-hidden="true"><circle cx="12" cy="12" r="10" fill="#ffffff"/><path d="M2 12h20M12 2c3 3 3 17 0 20M12 2c-3 3-3 17 0 20" fill="none" stroke="#1f93a6" stroke-width="1.5"/></svg>
          www.ventrinohomes.example
        </li>
      </ul>
    </div>
  </section>

  <section class="card card--back" aria-label="Business card back">
    <div class="feature-panel">
      <span class="feature-mark" aria-hidden="true"></span>
      <div class="feature-name">VENTRINO</div>
      <div class="feature-url">www.ventrinohomes.example</div>
    </div>
    <div class="faint-panel">
      <span class="brand-mark" aria-hidden="true"></span>
      <div class="brand-name">VENTRINO</div>
      <div class="brand-tagline">REAL ESTATE SERVICES</div>
    </div>
  </section>

</main>
</body>
</html>
```